TA BRAMLEY BUSINESS CARD DESIGN PROJECT

We need to utilize our logo that was expertly created on PixelHarbor and now need to match this with a business card design.

```html
<!DOCTYPE html>
<html lang="en">
<head>
<meta charset="utf-8">
<title>TA Bramley Business Card</title>
<link href="https://fonts.googleapis.com/css2?family=Open+Sans:wght@400;600;700&display=swap" rel="stylesheet">
<style>
  :root {
    --backdrop: #3b3b3b;
    --card: #161616;
    --brand-blue: #1f5fc4;
    --edge-blue: #1d5bd0;
    --text-light: #e6e6e6;
    --mark-grey: #4a4a4a;
  }
  * { box-sizing: border-box; margin: 0; padding: 0; }
  html, body {
    width: 1200px; height: 801px; overflow: hidden;
    background: var(--backdrop);
    font-family: "Open Sans", Arial, sans-serif;
  }
  .stage {
    position: relative; width: 1200px; height: 801px;
    display: flex; align-items: center; justify-content: center; gap: 60px;
  }
  .card {
    position: relative; width: 510px; height: 290px;
    background: var(--card);
    border: 2px solid var(--edge-blue);
    box-shadow: 0 14px 30px rgba(0,0,0,.35);
  }
  /* front */
  .brand-name {
    position: absolute; left: 34px; top: 58px;
    color: var(--brand-blue); font-weight: 700; font-size: 30px;
    letter-spacing: 3px; line-height: 1;
  }
  .identity {
    position: absolute; right: 34px; top: 52px; text-align: right;
  }
  .identity .person {
    color: var(--brand-blue); font-weight: 700; font-size: 19px;
    letter-spacing: .5px; text-transform: uppercase;
  }
  .identity .role {
    color: var(--text-light); font-size: 13px; margin-top: 2px;
  }
  .divider {
    position: absolute; left: 34px; right: 34px; top: 150px;
    height: 1px; background: var(--brand-blue);
  }
  .contact-list {
    position: absolute; left: 34px; bottom: 34px; list-style: none;
  }
  .contact-list li {
    display: flex; align-items: center; gap: 8px;
    color: var(--text-light); font-size: 14px; line-height: 22px;
  }
  .contact-list svg { width: 11px; height: 11px; fill: var(--brand-blue); flex: none; }
  .address {
    position: absolute; right: 34px; top: 166px; text-align: right;
    color: var(--text-light); font-size: 14px; line-height: 21px;
  }
  /* back */
  .back-mark {
    position: absolute; inset: 0;
    display: flex; align-items: center; justify-content: center;
    color: var(--mark-grey); font-weight: 700; font-size: 40px; letter-spacing: 4px;
  }
</style>
</head>
<body>
  <main class="stage">
    <section class="card card-front" aria-label="Business card front">
      <div class="brand-name">TA BRAMLEY</div>
      <div class="identity">
        <div class="person">Dorian Vale</div>
        <div class="role">President</div>
      </div>
      <div class="divider"></div>
      <div class="address">1840 Harbor Crest Dr<br>Lindenport CA 93001</div>
      <ul class="contact-list">
        <li>
          <svg viewBox="0 0 12 12" aria-hidden="true"><path d="M2.5 1l2 2.5-1 1.2c.6 1.3 1.5 2.2 2.8 2.8l1.2-1 2.5 2-1 1.5C5 10 2 7 1 2.5z"/></svg>
          555-014-2290
        </li>
        <li>
          <svg viewBox="0 0 12 12" aria-hidden="true"><path d="M1 3h10v7H1z M1 3l5 4 5-4" stroke="#161616" stroke-width=".8"/></svg>
          d.vale@tabramley.com
        </li>
        <li>
          <svg viewBox="0 0 12 12" aria-hidden="true"><circle cx="6" cy="6" r="5"/><path d="M1 6h10M6 1c-2 3-2 7 0 10M6 1c2 3 2 7 0 10" stroke="#161616" stroke-width=".8" fill="none"/></svg>
          www.tabramley.com
        </li>
      </ul>
    </section>
    <section class="card card-back" aria-label="Business card back">
      <div class="back-mark">TA BRAMLEY</div>
    </section>
  </main>
</body>
</html>
```